KLV Plant Services

We are a heavy diesel mechanical business with additional air con certificates, remapping engine rebuilt

Contact Information for Business Card

Company Name, Director Name, Managing Director, Contact details, email and website

Font styles to use
Serif
Script

```html
<!DOCTYPE html>
<html lang="en">
<head>
<meta charset="utf-8">
<title>KLV Plant Services – Business Card</title>
<link href="https://fonts.googleapis.com/css2?family=Arimo:wght@400;700&display=swap" rel="stylesheet">
<style>
  :root {
    --navy: #0a0a66;
    --paper: #f7f7f8;
    --ink: #222428;
    --stage: #d9d9db;
    --white: #ffffff;
    --rule: rgba(255,255,255,0.75);
  }
  * { box-sizing: border-box; margin: 0; padding: 0; }
  html, body { width: 1200px; height: 800px; overflow: hidden; }
  body {
    background: var(--stage);
    font-family: "Arimo", Arial, sans-serif;
    display: flex;
    align-items: center;
    justify-content: center;
    gap: 60px;
  }
  .card {
    width: 520px;
    height: 300px;
    border-radius: 22px;
    position: relative;
    overflow: hidden;
    box-shadow: 0 6px 18px rgba(0,0,0,0.15);
  }
  .card--back {
    background: var(--navy);
    color: var(--white);
    display: flex;
    align-items: center;
    justify-content: center;
  }
  .identity {
    text-align: right;
    padding-right: 22px;
  }
  .identity__name {
    font-weight: 700;
    font-size: 23px;
    letter-spacing: 0.2px;
  }
  .identity__role {
    font-size: 14px;
    margin-top: 3px;
  }
  .divider {
    width: 1px;
    height: 92px;
    background: var(--rule);
  }
  .contact {
    padding-left: 22px;
    font-size: 14px;
    line-height: 1.45;
  }
  .contact__address { margin-bottom: 6px; }
  .contact__label { font-weight: 700; display: inline-block; width: 26px; }
  .card--front {
    background: var(--paper);
    border-bottom: 4px solid var(--navy);
  }
  .brand {
    position: absolute;
    left: 0; right: 0; top: 92px;
    display: flex;
    align-items: center;
    justify-content: center;
    gap: 14px;
  }
  .brand__mark {
    width: 26px; height: 26px;
    border-radius: 50%;
    background: var(--navy);
  }
  .brand__name {
    font-weight: 700;
    font-size: 34px;
    color: var(--navy);
  }
  .front__web {
    position: absolute;
    left: 0; right: 0; bottom: 46px;
    text-align: center;
    font-size: 15px;
    letter-spacing: 3px;
    color: var(--ink);
  }
</style>
</head>
<body>
  <section class="card card--back">
    <div class="identity">
      <div class="identity__name">Daniel Morrow</div>
      <div class="identity__role">Managing Director</div>
    </div>
    <div class="divider"></div>
    <div class="contact">
      <div class="contact__address">2190 Harwell Road<br>Elm Ridge, NY 10452</div>
      <div><span class="contact__label">P :</span>(555) 0192-4418</div>
      <div><span class="contact__label">E :</span>name@klvplant.com</div>
      <div><span class="contact__label">W :</span>www.klvplant.com</div>
    </div>
  </section>

  <section class="card card--front">
    <div class="brand">
      <span class="brand__mark"></span>
      <span class="brand__name">KLV Plant Services</span>
    </div>
    <div class="front__web">www.klvplant.com</div>
  </section>
</body>
</html>
```